Upmarket Dessert Lounge needs a Business Card Design

We are an upmarket dessert lounge needing a business card to match our image.

We want something that is simple yet beautiful, feminine, classy, sophisticated and elegant. We want it to stand out and don't mind if it is bold.

The design should include our logo and colours of red or maroon with gold highlights. We don't mind if black is used.

Marlow & Quince

Target Market(s)

For those who like to indulge or treat themselves and give in to their temptations on good quality desserts.

Industry/Entity Type

Business

Requirements
Must have
• Must include our logo and our name

Marlow & Quince

M & Q

```html
<!DOCTYPE html>
<html lang="en">
<head>
<meta charset="utf-8">
<title>Marlow &amp; Quince — Business Card</title>
<link rel="stylesheet" href="https://fonts.googleapis.com/css2?family=Source+Sans+3:wght@400;600;700&display=swap">
<style>
  :root {
    --backdrop: #7b5238;
    --maroon: #7a1416;
    --maroon-dark: #6a1012;
    --cream: #f7dcaa;
    --gold: #f2c987;
    --paper: #ffffff;
    --ink: #3a3a3a;
  }
  * { box-sizing: border-box; margin: 0; padding: 0; }
  html, body { width: 1200px; height: 402px; overflow: hidden; }
  body {
    background: var(--backdrop);
    font-family: "Source Sans 3", "Myriad Pro", Arial, sans-serif;
    position: relative;
  }
  .card {
    position: absolute;
    top: 56px;
    width: 512px;
    height: 292px;
    border-radius: 16px;
    overflow: hidden;
  }
  .card--front { left: 61px; background: var(--paper); }
  .card--back { left: 639px; background: var(--maroon); }

  .front-wave { position: absolute; inset: 0; width: 100%; height: 100%; }

  .brand-name {
    position: absolute;
    left: 34px;
    top: 80px;
    width: 252px;
    text-align: center;
    font-size: 25px;
    font-weight: 600;
    letter-spacing: 0.5px;
    color: var(--maroon);
    white-space: nowrap;
  }

  .identity {
    position: absolute;
    right: 34px;
    top: 34px;
    text-align: right;
    color: var(--maroon);
  }
  .identity__name { font-size: 16px; font-weight: 700; line-height: 18px; }
  .identity__title { font-size: 12.5px; line-height: 15px; }

  .address {
    position: absolute;
    right: 34px;
    top: 98px;
    text-align: right;
    font-size: 13px;
    line-height: 14.5px;
    color: var(--ink);
  }

  .contacts {
    position: absolute;
    right: 18px;
    top: 212px;
    list-style: none;
    color: var(--paper);
    font-size: 12.5px;
    line-height: 18.5px;
  }
  .contacts li { display: flex; justify-content: flex-end; align-items: center; gap: 6px; }
  .contacts svg { width: 11px; height: 11px; flex: none; }

  .monogram {
    position: absolute;
    inset: 0;
    display: flex;
    align-items: center;
    justify-content: center;
    font-size: 78px;
    font-weight: 400;
    color: var(--cream);
    letter-spacing: 2px;
  }
</style>
</head>
<body>

<section class="card card--front" aria-label="Card front">
  <svg class="front-wave" viewBox="0 0 512 292" preserveAspectRatio="none" aria-hidden="true">
    <path d="M0 246 C120 262 250 235 340 200 C410 174 470 160 512 160 L512 292 L0 292 Z" fill="var(--maroon)"/>
    <path d="M0 244 C120 258 250 228 340 190 C410 162 470 150 512 152" fill="none" stroke="var(--gold)" stroke-width="3"/>
  </svg>

  <div class="brand-name">MARLOW &amp; QUINCE</div>

  <div class="identity">
    <p class="identity__name">Your name</p>
    <p class="identity__title">Title</p>
  </div>

  <address class="address" style="font-style:normal">
    Street Name<br>City Name<br>State Zip Code
  </address>

  <ul class="contacts">
    <li>555-014-2210
      <svg viewBox="0 0 12 12"><circle cx="6" cy="6" r="5.3" fill="none" stroke="var(--cream)" stroke-width="1"/><path d="M4 3.2 L5 3 L5.6 4.6 L4.9 5.1 Q5.6 6.6 6.9 7.2 L7.4 6.5 L9 7.1 L8.8 8.1 Q6 8.4 3.9 5.5 Q3.6 4.2 4 3.2Z" fill="var(--cream)"/></svg>
    </li>
    <li>555-014-2210
      <svg viewBox="0 0 12 12"><rect x="3.5" y="1" width="5" height="10" rx="1" fill="var(--cream)"/><rect x="4.4" y="2.2" width="3.2" height="3.6" fill="var(--maroon)"/></svg>
    </li>
    <li>info@marlowquince.com
      <svg viewBox="0 0 12 12"><rect x="1" y="3" width="10" height="6.5" fill="var(--cream)"/><path d="M1 3 L6 7 L11 3" fill="none" stroke="var(--maroon)" stroke-width="0.8"/></svg>
    </li>
    <li>www.marlowquince.com
      <svg viewBox="0 0 12 12"><circle cx="6" cy="6" r="5" fill="var(--cream)"/><g fill="none" stroke="var(--maroon)" stroke-width="0.7"><ellipse cx="6" cy="6" rx="2" ry="5"/><line x1="1" y1="6" x2="11" y2="6"/><line x1="6" y1="1" x2="6" y2="11"/></g></svg>
    </li>
  </ul>
</section>

<section class="card card--back" aria-label="Card back">
  <div class="monogram">M &amp; Q</div>
</section>

</body>
</html>
```